Book Cover for a book on Quiet Ventures

I am self-publishing my book on Brindlecart and need a book cover made. Below are the details. See attached templates for size we need to use. I also attached a previous cover we had made that I liked. The problem with it was they were two boys helping each other but the book is about women. I'm open to your ideas on the cover though, but I wanted to show you a style I liked as an idea.
Front of Cover
Book Title: Quiet Ventures
Book Subtitle: Unvarnished Notes of a Woman Founder
Author Name: Lorna T. Pelham
Add on the Spine of Cover: Quiet Ventures and Lorna T. Pelham
Back of the Cover Text:
Quiet Ventures: Unvarnished Notes of a Woman Founder is an honest account of a business owner’s experience attempting to navigate the start-up community while also pursuing spiritual growth. Author Lorna Pelham defines a spiritual entrepreneur as “someone who runs an enterprise with the purpose of growing love rather than material gain.” This book discusses the three dimensions of Quiet Ventures:
1. The business is an integral part of the founder’s spiritual journey.
2. Employees working for the spiritual enterprise, whether they know it or not, encounter this company because it's part of their spiritual path.
3. The business itself has a life force of its own and its purpose is to further the kingdom of heaven on earth.
These three dimensions happen simultaneously and work together to produce the greatest possible result. However, this can feel confusing to a founder juggling these dimensions while also trying to manage and run a business. This is not a formulaic self-help book or roadmap. Rather, it is a compilation of personal reflections that often seem at odds with the traditional world of entrepreneurship.
Below the description add my picture (see attached for my picture)
Bio text:
Lorna Pelham founded Halvex with the vision of ushering in a life-long education system that shifts away from standardization to one that empowers people to live their purpose. In college, Lorna interned for Open Meadow, a women’s empowerment initiative where she recognized her passion for helping people find their voice. Lorna's 20-year journey has come full circle to empowering other female CEOs who are pursuing the path of Quiet Ventures.
NOTE: Please note that Brindlecart puts a bar code on the bottom right of the back cover as is noted on the attached template.
Size template is attached to the brief, here are the sizes typed out:
# Description Width (in) Height (in)
1 Full Cover 12.79 9.25
2 Front Cover 6 9
3 Safe Area 5.875 8.75
4 Bleed 0.125 0.125
5 Margin 0.125 0.125
6 Spine 0.54 9
7 Spine Safe Area 0.415 8.75
8 Spine Margin 0.062 0.062
9 Barcode Margin 0.25 0.25
Pre-publication checklist
BRINDLECART TIPS for the final cover:
1. Save as a PDF. Your cover must be a single PDF that includes the back cover, spine, and front cover as one image.
2. Flatten all transparencies. These can cause the file to print with missing or distorted content. Consult your software's documentation to learn how.
3. Embed your fonts. Consult your software's documentation to learn how.
4. Remove crop marks, color bars, template text. Crop marks are lines showing where pages should be trimmed. Color bars are strips with a series of patches used to ensure color balance during printing. Also, remove any template text, PDF creation guides, or software references.
5. Ensure your cover image meets the minimum resolution of 300 DPI (dots per inch).
6. Optimize PDFs. Optimization is useful to reduce your file size, allowing for higher performance when transferring, uploading, viewing, and printing the files.
7. Remove file security. Locked or encrypted files will fail review.
Target Market(s)
Women who want to be CEOs or are currently CEOs of companies.
Industry/Entity Type
Entrepreneurship, business, spirituality
Requirements
Must have
- Just the text on the description. A very welcoming feel.
Nice to have
- I like the idea of having a sunrise/sunset in the image somehow like in the example I attached to the brief, but again I'm open.
Should not have
- Please don't put any yoga or meditation poses or hands outstretched. I have a lot of interesting ones that look like my example so if you are going to submit after Saturday 10/29, please only do so if you have a new idea! Thanks!

```html
<!DOCTYPE html>
<html lang="en">
<head>
<meta charset="utf-8">
<title>Quiet Ventures – Book Cover</title>
<link rel="stylesheet" href="https://fonts.googleapis.com/css2?family=Playfair+Display:wght@400;500&family=PT+Serif:ital,wght@0,400;0,700&display=swap">
<style>
  :root {
    --ink: #000000;
    --gold: #f5c518;
    --white: #ffffff;
    --photo-light: #c9ccd0;
    --photo-mid: #6f7379;
    --portrait: #c98a6a;
  }
  html, body { margin: 0; padding: 0; overflow: hidden; background: var(--ink); }
  .cover {
    position: relative; width: 1200px; height: 861px; overflow: hidden;
    background: var(--ink); color: var(--white);
    font-family: "PT Serif", "Times New Roman", serif;
  }
  .edge-band { position: absolute; left: 0; width: 1200px; height: 8px; background: var(--gold); }
  .edge-band.top { top: 0; }
  .edge-band.bottom { bottom: 0; }

  /* Back panel */
  .back { position: absolute; left: 0; top: 0; width: 563px; height: 861px; }
  .back-title {
    position: absolute; left: 0; top: 0; width: 563px; text-align: center; margin: 0;
    font-family: "Playfair Display", Georgia, serif; font-weight: 400; line-height: 1;
  }
  .back-title .main { display: block; color: var(--gold); font-size: 62px; letter-spacing: 1px; margin-top: 38px; }
  .back-title .second { display: block; color: var(--white); font-size: 28px; margin-top: 6px; }
  .blurb {
    position: absolute; left: 53px; top: 160px; width: 502px;
    font-size: 11.4px; line-height: 14.4px; text-align: justify;
  }
  .blurb p { margin: 0 0 12px; }
  .blurb ol { margin: 0 0 14px; padding-left: 22px; font-weight: 700; }
  .blurb li { padding-left: 8px; }
  .portrait-rule { position: absolute; top: 508px; height: 1px; background: var(--gold); }
  .portrait-rule.left { left: 86px; width: 134px; }
  .portrait-rule.right { left: 364px; width: 134px; }
  .portrait {
    position: absolute; left: 218px; top: 434px; width: 148px; height: 148px;
    border-radius: 50%; border: 2px solid var(--gold); box-sizing: border-box;
    background: radial-gradient(circle at 50% 40%, #d9a184, var(--portrait) 55%, #d94f5c 100%);
  }
  .bio {
    position: absolute; left: 104px; top: 632px; width: 380px; margin: 0;
    font-size: 11.4px; line-height: 14.8px; text-align: center;
  }

  /* Spine */
  .spine { position: absolute; left: 563px; top: 0; width: 60px; height: 861px; }
  .spine-text {
    position: absolute; left: 30px; white-space: nowrap; color: var(--gold);
    font-family: "Playfair Display", Georgia, serif; transform-origin: 0 0;
    transform: rotate(90deg) translateY(-50%);
  }
  .spine-title { top: 38px; font-size: 25px; letter-spacing: 1px; }
  .spine-author { top: 590px; font-size: 25px; }

  /* Front panel */
  .front { position: absolute; left: 623px; top: 0; width: 577px; height: 861px; }
  .front-photo {
    position: absolute; left: 3px; top: 8px; width: 574px; height: 460px;
    background: linear-gradient(180deg, var(--photo-light) 0%, #a9adb2 40%, var(--photo-mid) 70%, var(--ink) 100%);
  }
  .front-title {
    position: absolute; left: 0; top: 505px; width: 577px; margin: 0; text-align: center;
    font-family: "Playfair Display", Georgia, serif; font-weight: 400; line-height: 1;
  }
  .front-title .main { display: block; color: var(--gold); font-size: 84px; letter-spacing: 2px; }
  .front-title .second { display: block; color: var(--white); font-size: 36px; margin-top: 8px; }
  .front-rule { position: absolute; left: 60px; width: 457px; height: 1px; background: var(--gold); }
  .front-rule.upper { top: 686px; }
  .front-rule.lower { top: 733px; }
  .subtitle {
    position: absolute; left: 0; top: 694px; width: 577px; margin: 0; text-align: center;
    font-family: "Playfair Display", Georgia, serif; font-size: 23px; line-height: 28px; color: var(--white);
  }
  .author {
    position: absolute; left: 0; top: 776px; width: 577px; margin: 0; text-align: center;
    font-family: "Playfair Display", Georgia, serif; font-size: 40px; color: var(--gold);
  }
</style>
</head>
<body>
<div class="cover">
  <section class="back">
    <h2 class="back-title"><span class="main">QUIET</span><span class="second">VENTURES</span></h2>
    <div class="blurb">
      <p>Quiet Ventures: Unvarnished Notes of a Woman Founder is an honest account of a business owner’s experience attempting to navigate the start-up community while also pursuing spiritual growth. Author Lorna Pelham defines a spiritual entrepreneur as “someone who runs an enterprise with the purpose of growing love rather than material gain.” This book discusses the three dimensions of Quiet Ventures:</p>
      <ol>
        <li>The business is an integral part of the founder’s spiritual journey.</li>
        <li>Employees working for the spiritual enterprise, whether they know it or not, encounter this company because it's part of their spiritual path.</li>
        <li>The business itself has a life force of its own and its purpose is to further the kingdom of heaven on earth.</li>
      </ol>
      <p>These three dimensions happen simultaneously and work together to produce the greatest possible result. However, this can feel confusing to a founder juggling these dimensions while also trying to manage and run a business. This is not a formulaic self-help book or roadmap. Rather, it is a compilation of personal reflections that often seem at odds with the traditional world of entrepreneurship.</p>
    </div>
    <div class="portrait-rule left"></div>
    <div class="portrait" role="img" aria-label="Circular portrait photo of the author"></div>
    <div class="portrait-rule right"></div>
    <p class="bio">Lorna Pelham founded Halvex with the vision of ushering in a life-long education system that shifts away from standardization to one that empowers people to live their purpose. In college, Lorna interned for Open Meadow, a women’s empowerment initiative where she recognized her passion for helping people find their voice. Lorna's 20-year journey has come full circle to empowering other female CEOs who are pursuing the path of Quiet Ventures.</p>
  </section>

  <section class="spine">
    <div class="spine-text spine-title">QUIET VENTURES</div>
    <div class="spine-text spine-author">Lorna T. Pelham</div>
  </section>

  <section class="front">
    <div class="front-photo" role="img" aria-label="Photo of a businesswoman seated in a lounge chair with a laptop before tall city windows"></div>
    <h1 class="front-title"><span class="main">QUIET</span><span class="second">VENTURES</span></h1>
    <div class="front-rule upper"></div>
    <p class="subtitle">Unvarnished Notes of a Woman Founder</p>
    <div class="front-rule lower"></div>
    <p class="author">Lorna T. Pelham</p>
  </section>

  <div class="edge-band top"></div>
  <div class="edge-band bottom"></div>
</div>
</body>
</html>
```